Animal Eye Clinic needs a Business card

We are a new veterinary ophthalmology practice (Ridgeline Pet Vision Care) and we need a business card designed. We only see animal eyes - we are not a regular veterinary clinic. We already have a logo. We are looking for a professional, good looking business card to hand out to our clients. We are looking for something simple but professional and contemporary. Our logo is likely the only picture/graphic that needs to be on the card.
Updates

Contact Information for Business Card

Delia Vossman, BSc, DVM, MSc, DipACVO
Veterinary Ophthalmologist

Phone: 250.418.3927
Email: ridgelinepetvisioncare@mailbox-example.net
Website: ridgelinepetvisioncare-example.net
Address: 1874 Thornbury Rd
Kelowna, BC, V1X 4M9

Colors

Designer to choose colors to be used in the design.

Requirements
Must have
• Our logo (attached)

```html
<!DOCTYPE html>
<html lang="en">
<head>
<meta charset="utf-8">
<title>Ridgeline Pet Vision Care – Business Card</title>
<link rel="stylesheet" href="https://fonts.googleapis.com/css2?family=Arimo:wght@400;600&family=Crimson+Text&family=PT+Sans&display=swap">
<style>
  :root {
    --backdrop: #23272a;
    --teal: #00899a;
    --teal-deep: #007a89;
    --card-light: #ffffff;
    --card-shade: #d8d8d8;
    --ink-light: #f2f7f8;
    --ink-grey: #6b6b6b;
  }
  html, body {
    margin: 0;
    width: 1200px;
    height: 1176px;
    overflow: hidden;
    background: var(--backdrop);
  }
  .card {
    position: absolute;
    left: 280px;
    width: 617px;
    height: 353px;
    border-radius: 22px;
    overflow: hidden;
  }
  .card--front { top: 190px; background: linear-gradient(135deg, var(--card-shade), var(--card-light) 60%); }
  .card--back  { top: 589px; background: linear-gradient(30deg, var(--card-shade), var(--card-light) 75%); }
  .front-art { position: absolute; inset: 0; }
  .holder {
    position: absolute;
    left: 35px;
    top: 27px;
    color: var(--ink-light);
  }
  .holder__name {
    font-family: "Arimo", Arial, sans-serif;
    font-size: 20px;
    letter-spacing: 0.3px;
    margin: 0;
  }
  .holder__name small { font-size: 14px; }
  .holder__role {
    font-family: "Crimson Text", Georgia, serif;
    font-size: 15.5px;
    margin: 0;
  }
  .contacts {
    position: absolute;
    left: 35px;
    top: 222px;
    margin: 0;
    padding: 0;
    list-style: none;
    font-family: "PT Sans", Arial, sans-serif;
    font-size: 14px;
    color: var(--ink-light);
  }
  .contacts li {
    display: flex;
    align-items: center;
    gap: 8px;
    height: 26px;
  }
  .contacts svg { width: 13px; height: 13px; fill: var(--ink-light); }
  .contacts .address { margin-top: 9px; }
  .brand {
    position: absolute;
    left: 130px;
    top: 140px;
    display: flex;
    align-items: center;
    gap: 18px;
  }
  .brand__dot {
    width: 60px; height: 60px;
    border-radius: 50%;
    background: var(--teal);
  }
  .brand__name {
    font-family: "Arimo", Arial, sans-serif;
    font-weight: 600;
    font-size: 27px;
    line-height: 1.1;
    color: var(--teal);
    text-transform: uppercase;
    letter-spacing: 1px;
  }
</style>
</head>
<body>
  <section class="card card--front">
    <svg class="front-art" viewBox="0 0 617 353" aria-hidden="true">
      <polygon points="0,0 470,0 360,353 0,353" fill="var(--teal-deep)"/>
      <polygon points="0,0 470,0 420,160 0,160" fill="var(--teal)" opacity="0.5"/>
      <circle cx="500" cy="176" r="80" fill="var(--teal)"/>
    </svg>
    <div class="holder">
      <p class="holder__name">DELIA VOSSMAN, <small>BSC, DVM, MSC, DIPACVO</small></p>
      <p class="holder__role">Veterinary Ophthalmologist</p>
    </div>
    <ul class="contacts">
      <li><svg viewBox="0 0 16 16"><path d="M1 5c0-2 3-3 7-3s7 1 7 3v2h-4V5H5v2H1zM3 8h10l1 6H2z"/></svg>250.418.3927</li>
      <li><svg viewBox="0 0 16 16"><path d="M1 3h14v10H1zM2 4l6 5 6-5" stroke="#007a89" stroke-width="1.2"/></svg>ridgelinepetvisioncare@mailbox-example.net</li>
      <li><svg viewBox="0 0 16 16"><circle cx="8" cy="8" r="6.5" fill="none" stroke="#f2f7f8" stroke-width="1.2"/><path d="M1.5 8h13M8 1.5v13" stroke="#f2f7f8" stroke-width="1"/></svg>ridgelinepetvisioncare-example.net</li>
      <li class="address">1874 Thornbury Rd, Kelowna, BC, V1X 4M9</li>
    </ul>
  </section>

  <section class="card card--back">
    <div class="brand">
      <span class="brand__dot"></span>
      <span class="brand__name">Ridgeline<br>Pet Vision Care</span>
    </div>
  </section>
</body>
</html>
```